Keystone Trench Co Business Card*

Looking for a professional, clean and crisp business card

I am in the underground utilities industry and am just looking for a really impressive business card. I would like our card to be white with our symbol crisp and clear with it protruding. I also have a business partner that will require his name and info on the card once the design is set. I would like to have our website info on the card which is;
http://keystonetrenchco.example/

Contact Information for Business Card

Website, contact name, number and email

```html
<!DOCTYPE html>
<html lang="en">
<head>
<meta charset="utf-8">
<title>Keystone Trench Co — Business Card</title>
<link href="https://fonts.googleapis.com/css2?family=Lato:wght@400;700;900&display=swap" rel="stylesheet">
<style>
  :root {
    --backdrop: #d6d6d6;
    --card-white: #ffffff;
    --card-black: #000000;
    --ink: #111111;
    --muted: #555555;
    --brand-blue: #3a5ca8;
    --paper-text: #ffffff;
  }
  * { box-sizing: border-box; margin: 0; padding: 0; }
  html, body {
    width: 1200px;
    height: 1143px;
    overflow: hidden;
    background: var(--backdrop);
    font-family: "Lato", sans-serif;
  }
  .card {
    position: absolute;
    left: 298px;
    width: 603px;
    height: 344px;
  }
  .card--front { top: 180px; background: var(--card-white); }
  .card--back  { top: 620px; background: var(--card-black); }

  .wordmark {
    position: absolute;
    display: flex;
    flex-direction: column;
    align-items: center;
    justify-content: center;
    gap: 10px;
    text-align: center;
    font-family: "Lato", sans-serif;
    font-weight: 900;
    text-transform: uppercase;
    line-height: 1.1;
  }
  .wordmark__dot {
    width: 14px;
    height: 14px;
    border-radius: 50%;
    background: currentColor;
  }
  .card--front .wordmark {
    left: 103px; top: 101px; width: 160px; height: 140px;
    color: var(--ink);
    font-size: 22px;
  }
  .card--back .wordmark {
    left: 196px; top: 77px; width: 211px; height: 190px;
    color: var(--paper-text);
    font-size: 30px;
  }

  .divider {
    position: absolute;
    left: 302px; top: 97px;
    width: 1px; height: 149px;
    background: var(--ink);
  }

  .contact {
    position: absolute;
    left: 343px; top: 92px;
    color: var(--muted);
  }
  .contact__name {
    font-size: 25px;
    font-weight: 900;
    color: var(--ink);
    line-height: 1;
    letter-spacing: -0.2px;
  }
  .contact__name .surname { color: var(--brand-blue); }
  .contact__role {
    margin-top: 6px;
    font-size: 14.5px;
    line-height: 1;
  }
  .contact__address {
    margin-top: 13px;
    margin-left: -2px;
    font-size: 14.5px;
    line-height: 18px;
    font-style: normal;
  }
  .contact__list {
    list-style: none;
    margin-top: 8px;
    margin-left: -2px;
  }
  .contact__item {
    display: flex;
    align-items: center;
    height: 20px;
    font-size: 14.5px;
  }
  .contact__icon {
    width: 14px; height: 14px;
    margin-right: 12px;
    color: var(--ink);
    flex: none;
  }
</style>
</head>
<body>

<section class="card card--front" aria-label="Business card front">
  <div class="wordmark">
    <span>Keystone<br>Trench Co</span>
    <span class="wordmark__dot"></span>
  </div>

  <div class="divider"></div>

  <div class="contact">
    <h1 class="contact__name">Dale <span class="surname">Morrow</span></h1>
    <p class="contact__role">Owner</p>
    <address class="contact__address">
      1234 First Line Address<br>
      5678 Second Line Address
    </address>
    <ul class="contact__list">
      <li class="contact__item">
        <svg class="contact__icon" viewBox="0 0 24 24" aria-hidden="true">
          <path fill="currentColor" d="M6.6 10.8a15.1 15.1 0 0 0 6.6 6.6l2.2-2.2c.3-.3.7-.4 1-.2 1.1.4 2.3.6 3.6.6.6 0 1 .4 1 1V20c0 .6-.4 1-1 1C10.6 21 3 13.4 3 4c0-.6.4-1 1-1h3.5c.6 0 1 .4 1 1 0 1.3.2 2.5.6 3.6.1.3 0 .7-.2 1z"/>
          <path fill="none" stroke="currentColor" stroke-width="2" d="M14 3a7 7 0 0 1 7 7M14 7a3 3 0 0 1 3 3"/>
        </svg>
        604-555-0182
      </li>
      <li class="contact__item">
        <svg class="contact__icon" viewBox="0 0 24 24" aria-hidden="true">
          <rect x="2" y="5" width="20" height="14" fill="currentColor"/>
          <path d="M2 5l10 8 10-8M2 19l8-7M22 19l-8-7" fill="none" stroke="#fff" stroke-width="1.6"/>
        </svg>
        Dale@keystonetrenchco.example
      </li>
      <li class="contact__item">
        <svg class="contact__icon" viewBox="0 0 24 24" aria-hidden="true">
          <g fill="none" stroke="currentColor" stroke-width="1.6">
            <circle cx="12" cy="12" r="10"/>
            <ellipse cx="12" cy="12" rx="4.5" ry="10"/>
            <path d="M2 12h20M4 7h16M4 17h16"/>
          </g>
        </svg>
        www.keystonetrenchco.example
      </li>
    </ul>
  </div>
</section>

<section class="card card--back" aria-label="Business card back">
  <div class="wordmark">
    <span>Keystone<br>Trench Co</span>
    <span class="wordmark__dot"></span>
  </div>
</section>

</body>
</html>
```